American cannabis tech company business card design

Pavrel.com is seeking a modern, professional, and brand-aligned business card that represents our company and its core values: Mission, Story, Values, and Impact. As an innovative cannabis company, we want a business card that is not only visually appealing but also serves as a representation of who we are and what we stand for.

Project Scope: Design a double-sided business card that integrates our brand identity and core values. Incorporate our key brand elements, ensuring a sleek and contemporary aesthetic. Visually reflect our core values (Mission, Story, Values, Impact) in a way that is engaging yet professional.

Target Market(s)

Vendors, third parties,

Contact Information for Business Card

Contact details (name, title, email, phone, website, etc.)

Font styles to use
Other font styles liked:
• Caslon, Centra

Colors

Designer to choose colors to be used in the design.

Requirements
Must have
• Pavrel.com logo and branding A creative yet clean way to integrate our core values (Mission, Story, Values, Impact) Modern typography and a well-structured layout
Nice to have
• forest green, grey, white, black
Should not have
• references to marijuana, leafs, plants, or related product

```html
<!DOCTYPE html>
<html lang="en">
<head>
<meta charset="utf-8">
<title>Pavrel.com Business Card</title>
<link href="https://fonts.googleapis.com/css2?family=Poppins:wght@400;600;700&display=swap" rel="stylesheet">
<style>
  :root {
    --stage: #202020;
    --forest: #183a1d;
    --forest-deep: #122d16;
    --forest-light: #2b6a33;
    --paper: #ffffff;
    --ink: #183a1d;
  }
  * { margin: 0; padding: 0; box-sizing: border-box; }
  html, body {
    width: 1200px;
    height: 1015px;
    overflow: hidden;
    background: var(--stage);
    font-family: "Poppins", sans-serif;
  }
  .canvas {
    position: relative;
    width: 1200px;
    height: 1015px;
  }
  .card {
    position: absolute;
    left: 270px;
    width: 660px;
    height: 377px;
    overflow: hidden;
    box-shadow: 0 18px 40px rgba(0,0,0,0.55);
  }
  .card-back { top: 90px; background: var(--forest); }
  .card-front { top: 540px; background: var(--paper); }

  .back-pattern {
    position: absolute;
    inset: 0;
    background: linear-gradient(135deg, var(--forest-deep) 0%, var(--forest) 55%, var(--forest-light) 100%);
  }
  .back-wordmark {
    position: absolute;
    left: 440px;
    top: 180px;
    color: var(--paper);
    font-weight: 700;
    font-size: 26px;
    letter-spacing: 0.5px;
  }

  .front-wave { position: absolute; inset: 0; }
  .front-wordmark {
    position: absolute;
    left: 42px;
    top: 130px;
    color: var(--ink);
    font-weight: 700;
    font-size: 72px;
    line-height: 1;
    letter-spacing: 1px;
  }
  .holder {
    position: absolute;
    right: 36px;
    top: 42px;
    text-align: right;
    color: var(--ink);
  }
  .holder-name { font-weight: 700; font-size: 22px; letter-spacing: 1px; line-height: 1.1; }
  .holder-title { font-weight: 400; font-size: 17px; line-height: 1.2; }

  .contact {
    position: absolute;
    right: 28px;
    top: 205px;
    list-style: none;
    color: var(--paper);
    font-size: 19px;
    line-height: 1.45;
  }
  .contact li { display: flex; justify-content: flex-end; align-items: center; gap: 8px; }
  .contact svg { width: 16px; height: 16px; flex: none; }
</style>
</head>
<body>
<main class="canvas">

  <section class="card card-back">
    <div class="back-pattern" role="img" aria-label="Repeating brand wordmark pattern in tonal greens"></div>
    <span class="back-wordmark">PAVREL</span>
  </section>

  <section class="card card-front">
    <svg class="front-wave" viewBox="0 0 660 377" aria-hidden="true">
      <path d="M0,300 C150,330 300,320 380,220 C450,130 540,92 660,86 L660,377 L0,377 Z" fill="var(--forest)"/>
      <path d="M0,312 C160,340 310,332 390,232 C460,146 548,104 660,98" fill="none" stroke="var(--paper)" stroke-width="5"/>
      <path d="M0,330 C170,356 320,346 400,248 C470,164 556,120 660,114" fill="none" stroke="var(--paper)" stroke-width="5"/>
    </svg>

    <div class="holder">
      <p class="holder-name">DANIEL HARPER</p>
      <p class="holder-title">Managing Director</p>
    </div>

    <span class="front-wordmark">PAVREL</span>

    <ul class="contact">
      <li>044-555 010 234
        <svg viewBox="0 0 16 16"><path d="M4 1.5 L6.5 4.5 L5 6.5 C6 8.5 7.5 10 9.5 11 L11.5 9.5 L14.5 12 L13 14.5 C7 14 2 9 1.5 3 Z" fill="var(--paper)"/></svg>
      </li>
      <li>info@pavrel.com
        <svg viewBox="0 0 16 16"><rect x="1" y="3" width="14" height="10" fill="var(--paper)"/><path d="M1 3 L8 9 L15 3" fill="none" stroke="var(--forest)" stroke-width="1.3"/></svg>
      </li>
      <li>www.pavrel.com
        <svg viewBox="0 0 16 16"><circle cx="8" cy="8" r="7" fill="var(--paper)"/><g fill="none" stroke="var(--forest)" stroke-width="1"><ellipse cx="8" cy="8" rx="3" ry="7"/><path d="M1 8 H15 M2.5 4.5 H13.5 M2.5 11.5 H13.5"/></g></svg>
      </li>
    </ul>
  </section>

</main>
</body>
</html>
```